PAX

We need to design a power point presentation that can englobe all our company products.

This presentation has to have all the required to be used as template for future presentations.

We focus on prodcut developing for supermarkets, ( we help them with their own brand products ex. Sunny Harvest, TK, etc.)
Also we are on the marine industry, we develop ships and oil rigs for the Oil and deep water market.

Target Market(s)

Oil Companies
Supermarket companies
Retail Companies

Industry/Entity Type

It Company

Requirements
Must have
• Our Logo and company colors
Nice to have
• Something describing globalization.
Should not have
• Orange color

```html
<!DOCTYPE html>
<html lang="en">
<head>
<meta charset="utf-8">
<title>PAX Presentation Template</title>
<link rel="stylesheet" href="https://fonts.googleapis.com/css2?family=Open+Sans:wght@400;600&family=Roboto+Condensed:wght@700&display=swap">
<style>
  :root {
    --title-cyan: #1ba6ea;
    --brand-navy: #2f4f8c;
    --bullet-navy: #3c5f97;
    --text-dark: #474747;
    --header-top: #ffffff;
    --header-bottom: #f3f3f4;
    --body-top: #f8f8f9;
    --body-bottom: #ececed;
    --rule-grey: #cfcfd2;
    --footer-fill: #dfe4ea;
    --footer-rule: #3a5f9c;
    --logo-green: #7cc242;
  }
  * { margin: 0; padding: 0; box-sizing: border-box; }
  html, body { width: 1200px; height: 900px; overflow: hidden; }
  body { font-family: "Open Sans", Arial, sans-serif; color: var(--text-dark); }

  .slide {
    position: relative;
    width: 1200px;
    height: 900px;
    background: linear-gradient(var(--body-top), var(--body-bottom));
    overflow: hidden;
  }

  .slide-header {
    position: absolute;
    left: 0; top: 0;
    width: 1200px; height: 106px;
    background: linear-gradient(var(--header-top), var(--header-bottom));
    border-bottom: 1.5px solid var(--rule-grey);
  }
  .slide-title {
    position: absolute;
    left: 45px; top: 28px;
    font-family: "Roboto Condensed", "Arial Narrow", sans-serif;
    font-weight: 700;
    font-size: 46px;
    line-height: 1;
    color: var(--title-cyan);
    letter-spacing: 0.3px;
  }

  .brand-tab {
    position: absolute;
    left: 1062px; top: -2px;
    width: 124px; height: 180px;
    background: #ffffff;
    border: 1.5px solid var(--rule-grey);
    border-top: none;
    border-radius: 0 0 62px 62px;
    box-shadow: 0 2px 4px rgba(0,0,0,0.08);
    display: flex;
    flex-direction: column;
    align-items: center;
    justify-content: center;
    gap: 12px;
    padding-bottom: 10px;
  }
  .brand-dot {
    width: 40px; height: 40px;
    border-radius: 50%;
    background: var(--title-cyan);
  }
  .brand-name {
    font-family: "Open Sans", Arial, sans-serif;
    font-weight: 600;
    font-size: 30px;
    line-height: 1;
    color: var(--logo-green);
  }

  .content {
    position: absolute;
    left: 0; top: 0;
    width: 1200px;
  }
  .topic {
    position: absolute;
    left: 58px;
  }
  .topic-heading {
    display: flex;
    align-items: center;
    height: 40px;
  }
  .topic-icon {
    width: 44px; height: 44px;
    flex: none;
  }
  .topic-heading h2 {
    margin-left: 21px;
    font-weight: 400;
    font-size: 24px;
    color: var(--text-dark);
    white-space: nowrap;
  }
  .point-list {
    list-style: none;
    margin-top: 33px;
    margin-left: 66px;
  }
  .point-list li {
    position: relative;
    padding-left: 24px;
    font-weight: 600;
    font-size: 18.5px;
    line-height: 28.5px;
    color: var(--text-dark);
    white-space: nowrap;
    height: 87px;
  }
  .point-list li:last-child { height: auto; }
  .chevron {
    position: absolute;
    left: 6px; top: 7px;
    width: 12px; height: 15px;
  }

  .slide-footer {
    position: absolute;
    left: 0; top: 848px;
    width: 1200px; height: 52px;
    background: var(--footer-fill);
    border-top: 2.5px solid var(--footer-rule);
    display: flex;
    align-items: center;
    justify-content: space-between;
    padding: 0 12px 0 36px;
    font-size: 18px;
    color: var(--text-dark);
  }
</style>
</head>
<body>
<div class="slide">
  <header class="slide-header">
    <h1 class="slide-title">Presentation Title Here</h1>
  </header>

  <div class="brand-tab">
    <span class="brand-dot"></span>
    <span class="brand-name">PAX</span>
  </div>

  <main class="content">
    <section class="topic" style="top:165px">
      <div class="topic-heading">
        <svg class="topic-icon" viewBox="0 0 44 44" aria-hidden="true">
          <circle cx="22" cy="23" r="20" fill="rgba(0,0,0,0.18)"/>
          <circle cx="22" cy="22" r="20" fill="#ffffff"/>
          <circle cx="22" cy="22" r="16.5" fill="var(--bullet-navy)"/>
          <circle cx="22" cy="22" r="9.5" fill="none" stroke="#ffffff" stroke-width="2.2"/>
          <path d="M16.5 22h10M22.5 17.5l4.5 4.5-4.5 4.5" fill="none" stroke="#ffffff" stroke-width="2.4" stroke-linecap="round" stroke-linejoin="round"/>
        </svg>
        <h2>Lorem ipsum dolor sit ipsum Lorem ipsum dolor sit ipsum Lorem ipsum</h2>
      </div>
      <ul class="point-list">
        <li><svg class="chevron" viewBox="0 0 12 15" aria-hidden="true"><path d="M2 1.5l7 6-7 6" fill="none" stroke="var(--bullet-navy)" stroke-width="3"/></svg>Lorem ipsum dolor sit ipsum Lorem ipsum dolor sit ipsum Lorem ipsum&nbsp; Lorem ipsum dolor<br>sit ipsum Lorem ipsum dolor sit ipsum Lorem ipsum</li>
        <li><svg class="chevron" viewBox="0 0 12 15" aria-hidden="true"><path d="M2 1.5l7 6-7 6" fill="none" stroke="var(--bullet-navy)" stroke-width="3"/></svg>Lorem ipsum dolor sit ipsum Lorem ipsum dolor sit ipsum Lorem ipsum&nbsp; Lorem ipsum dolor<br>sit ipsum Lorem ipsum dolor sit ipsum Lorem ipsum</li>
        <li><svg class="chevron" viewBox="0 0 12 15" aria-hidden="true"><path d="M2 1.5l7 6-7 6" fill="none" stroke="var(--bullet-navy)" stroke-width="3"/></svg>Lorem ipsum dolor sit ipsum Lorem ipsum dolor sit ipsum Lorem ipsum&nbsp; Lorem ipsum dolor<br>sit ipsum Lorem ipsum dolor sit ipsum Lorem ipsum</li>
      </ul>
    </section>

    <section class="topic" style="top:478px">
      <div class="topic-heading">
        <svg class="topic-icon" viewBox="0 0 44 44" aria-hidden="true">
          <circle cx="22" cy="23" r="20" fill="rgba(0,0,0,0.18)"/>
          <circle cx="22" cy="22" r="20" fill="#ffffff"/>
          <circle cx="22" cy="22" r="16.5" fill="var(--bullet-navy)"/>
          <circle cx="22" cy="22" r="9.5" fill="none" stroke="#ffffff" stroke-width="2.2"/>
          <path d="M16.5 22h10M22.5 17.5l4.5 4.5-4.5 4.5" fill="none" stroke="#ffffff" stroke-width="2.4" stroke-linecap="round" stroke-linejoin="round"/>
        </svg>
        <h2>Lorem ipsum dolor sit ipsum Lorem ipsum dolor sit ipsum Lorem ipsum</h2>
      </div>
      <ul class="point-list">
        <li><svg class="chevron" viewBox="0 0 12 15" aria-hidden="true"><path d="M2 1.5l7 6-7 6" fill="none" stroke="var(--bullet-navy)" stroke-width="3"/></svg>Lorem ipsum dolor sit ipsum Lorem ipsum dolor sit ipsum Lorem ipsum&nbsp; Lorem ipsum dolor<br>sit ipsum Lorem ipsum dolor sit ipsum Lorem ipsum</li>
        <li><svg class="chevron" viewBox="0 0 12 15" aria-hidden="true"><path d="M2 1.5l7 6-7 6" fill="none" stroke="var(--bullet-navy)" stroke-width="3"/></svg>Lorem ipsum dolor sit ipsum Lorem ipsum dolor sit ipsum Lorem ipsum&nbsp; Lorem ipsum dolor<br>sit ipsum Lorem ipsum dolor sit ipsum Lorem ipsum</li>
        <li><svg class="chevron" viewBox="0 0 12 15" aria-hidden="true"><path d="M2 1.5l7 6-7 6" fill="none" stroke="var(--bullet-navy)" stroke-width="3"/></svg>Lorem ipsum dolor sit ipsum Lorem ipsum dolor sit ipsum Lorem ipsum&nbsp; Lorem ipsum dolor<br>sit ipsum Lorem ipsum dolor sit ipsum Lorem ipsum</li>
      </ul>
    </section>
  </main>

  <footer class="slide-footer">
    <span class="page-number">Page : 01</span>
    <span class="copyright">Copyright Text here</span>
  </footer>
</div>
</body>
</html>
```